MRT Property - Business Cards

Looking for a business card & general letterhead, signage etc design for our new logo.

Colours:
000a20
0056a2
00b5ef
0088ce
68cef2

Fonts:
Poppins
Karla

Please keep look and feel of new brand - example in the zip package I sent.

```html
<!DOCTYPE html>
<html lang="en">
<head>
<meta charset="UTF-8">
<title>MRT Property – Business Cards</title>
<link rel="stylesheet" href="https://fonts.googleapis.com/css2?family=Karla:wght@400;500&family=Poppins:wght@300;400;600&display=swap">
<style>
  :root {
    --navy: #000a20;
    --blue: #0056a2;
    --cyan: #00b5ef;
    --mid-blue: #0088ce;
    --sky: #68cef2;
    --paper: #ffffff;
    --backdrop: #e6e3de;
    --text-dark: #2a3240;
  }
  * { margin: 0; padding: 0; box-sizing: border-box; }
  html, body { width: 900px; height: 1200px; overflow: hidden; }
  body {
    background: var(--backdrop);
    position: relative;
    font-family: "Karla", sans-serif;
  }
  .card {
    position: absolute;
    left: 99px;
    width: 702px;
    height: 534px;
    border-radius: 28px;
    overflow: hidden;
    box-shadow: 0 10px 28px rgba(0, 10, 32, 0.25);
  }
  .card-front { top: 36px; background: var(--paper); }
  .card-back {
    top: 630px;
    background: linear-gradient(160deg, #0a66b8 0%, var(--blue) 70%, #004d93 100%);
    display: flex;
    align-items: center;
    justify-content: center;
  }
  .brand-name {
    font-family: "Poppins", sans-serif;
    font-weight: 600;
    letter-spacing: 1px;
    white-space: nowrap;
  }
  .card-front .brand-name {
    position: absolute;
    left: 40px;
    top: 236px;
    font-size: 36px;
    color: var(--blue);
  }
  .card-back .brand-name {
    font-size: 66px;
    color: var(--paper);
  }
  .divider {
    position: absolute;
    left: 327px;
    top: 120px;
    width: 2px;
    height: 270px;
    background: var(--mid-blue);
  }
  .contact-block {
    position: absolute;
    left: 345px;
    top: 118px;
    color: var(--text-dark);
  }
  .person-name {
    font-family: "Poppins", sans-serif;
    font-weight: 400;
    font-size: 30px;
    line-height: 1.1;
    color: var(--blue);
  }
  .person-title {
    font-size: 17px;
    margin-top: 6px;
    color: var(--text-dark);
  }
  .address {
    font-size: 17px;
    line-height: 1.35;
    margin-top: 26px;
  }
  .contact-list { list-style: none; margin-top: 26px; }
  .contact-item {
    display: flex;
    align-items: center;
    gap: 12px;
    font-size: 17px;
    height: 36px;
  }
  .contact-item svg { width: 18px; height: 18px; flex: none; }
  .accent-band {
    position: absolute;
    left: 0; right: 0; bottom: 0;
    height: 24px;
    display: flex;
  }
  .accent-band span { flex: 1; }
  .band-1 { background: var(--sky); flex: 1.6 !important; }
  .band-2 { background: var(--cyan); }
  .band-3 { background: var(--mid-blue); flex: 1.4 !important; }
  .band-4 { background: var(--cyan); }
  .band-5 { background: var(--blue); flex: 1.2 !important; }
</style>
</head>
<body>
  <section class="card card-front" aria-label="Business card front">
    <div class="brand-name">MRT Property</div>
    <div class="divider"></div>
    <div class="contact-block">
      <h1 class="person-name">Daniel Hart</h1>
      <p class="person-title">Managing Director</p>
      <p class="address">420 Maple Ridge Ave Suite<br>210 Columbus Ohio 43215</p>
      <ul class="contact-list">
        <li class="contact-item">
          <svg viewBox="0 0 24 24" aria-hidden="true"><path fill="#0056a2" d="M6.6 10.8a15.1 15.1 0 0 0 6.6 6.6l2.2-2.2c.3-.3.7-.4 1-.2 1.1.4 2.3.6 3.6.6.6 0 1 .4 1 1V20c0 .6-.4 1-1 1A17 17 0 0 1 3 4c0-.6.4-1 1-1h3.5c.6 0 1 .4 1 1 0 1.3.2 2.5.6 3.6.1.3 0 .7-.2 1z"/></svg>
          1 (555) 214-7390
        </li>
        <li class="contact-item">
          <svg viewBox="0 0 24 24" aria-hidden="true"><rect x="2" y="5" width="20" height="14" rx="2" fill="#0056a2"/><path d="M3 6.5l9 6 9-6" fill="none" stroke="#fff" stroke-width="1.6"/></svg>
          info@mrtproperty.com
        </li>
        <li class="contact-item">
          <svg viewBox="0 0 24 24" aria-hidden="true"><circle cx="12" cy="12" r="10" fill="#0056a2"/><path d="M2 12h20M12 2c3 3 3 17 0 20M12 2c-3 3-3 17 0 20" fill="none" stroke="#fff" stroke-width="1.3"/></svg>
          www.mrtproperty.com
        </li>
      </ul>
    </div>
    <div class="accent-band">
      <span class="band-1"></span><span class="band-2"></span><span class="band-3"></span><span class="band-4"></span><span class="band-5"></span>
    </div>
  </section>

  <section class="card card-back" aria-label="Business card back">
    <div class="brand-name">MRT Property</div>
  </section>
</body>
</html>
```